BRIGHT RIVER POWER.

I'd like my business logo.
contact name: Dennis Halvorsen
phone:0438759164
email: info@brightriverpower.net.au
website: www.brightriverpower.net.au

services:
solar
battery storage
LED lighting
energy saving solutions
general electrical
I'd like the design to look professional

Target Market(s)

Everyone

Industry/Entity Type

Business

Contact Information for Business Card

as described above

Requirements
Must have
• Id like the colours and the design to work well with my logo.

```html
<!DOCTYPE html>
<html lang="en">
<head>
<meta charset="utf-8">
<title>Bright River Power – Business Card</title>
<link rel="stylesheet" href="https://fonts.googleapis.com/css2?family=Montserrat:wght@400;500;700&display=swap">
<style>
  :root {
    --page-bg: #d8d3ca;
    --card-black: #0c0c0c;
    --card-edge: #1c1c1c;
    --sun-gold: #8a6a2a;
    --accent-orange: #f7941d;
    --brand-green: #9cc43f;
    --text-white: #f2f2f2;
    --divider: #cfcfcf;
  }
  * { margin: 0; padding: 0; box-sizing: border-box; }
  html, body {
    width: 1200px;
    height: 1022px;
    overflow: hidden;
  }
  body {
    background: var(--page-bg);
    font-family: "Montserrat", Arial, sans-serif;
    position: relative;
  }
  .business-card {
    position: absolute;
    left: 150px;
    top: 254px;
    width: 900px;
    height: 514px;
    border-radius: 22px;
    background: linear-gradient(160deg, var(--card-edge) 0%, var(--card-black) 55%, #050505 100%);
    overflow: hidden;
    box-shadow: 0 18px 40px rgba(0,0,0,0.35);
  }
  .sunburst-decoration {
    position: absolute;
    left: -120px;
    top: -60px;
    width: 640px;
    height: 640px;
  }
  .brand-lockup {
    position: absolute;
    left: 56px;
    top: 212px;
    width: 380px;
    display: flex;
    align-items: center;
    gap: 18px;
  }
  .brand-dot {
    width: 52px;
    height: 52px;
    border-radius: 50%;
    background: var(--sun-gold);
    flex: none;
  }
  .brand-name {
    font-weight: 700;
    font-size: 34px;
    letter-spacing: 1px;
    color: var(--brand-green);
    line-height: 1.12;
    max-width: 290px;
  }
  .column-divider {
    position: absolute;
    left: 468px;
    top: 50px;
    width: 2px;
    height: 414px;
    background: linear-gradient(180deg, transparent 0%, var(--divider) 50%, transparent 100%);
  }
  .contact-column {
    position: absolute;
    left: 504px;
    top: 58px;
    width: 370px;
    color: var(--text-white);
  }
  .contact-name {
    font-weight: 700;
    font-size: 34px;
    color: var(--accent-orange);
    margin-bottom: 16px;
  }
  .contact-list, .service-list { list-style: none; }
  .contact-item {
    display: flex;
    align-items: center;
    gap: 12px;
    font-size: 18px;
    font-weight: 500;
    line-height: 32px;
  }
  .contact-icon { width: 16px; height: 16px; flex: none; }
  .web-domain { color: var(--accent-orange); }
  .service-list { margin-top: 20px; }
  .service-item {
    display: flex;
    align-items: center;
    gap: 16px;
    font-size: 21px;
    line-height: 37px;
  }
  .service-item::before {
    content: "";
    width: 11px;
    height: 11px;
    border-radius: 50%;
    background: var(--accent-orange);
    flex: none;
  }
</style>
</head>
<body>
  <article class="business-card">
    <svg class="sunburst-decoration" viewBox="0 0 640 640" role="img" aria-label="Faint golden sunburst with arc decoration">
      <defs>
        <radialGradient id="sunGlow" cx="50%" cy="50%" r="50%">
          <stop offset="0%" stop-color="#8a6a2a" stop-opacity="0.55"/>
          <stop offset="60%" stop-color="#6b5220" stop-opacity="0.25"/>
          <stop offset="100%" stop-color="#0c0c0c" stop-opacity="0"/>
        </radialGradient>
      </defs>
      <circle cx="320" cy="320" r="320" fill="url(#sunGlow)"/>
    </svg>

    <div class="brand-lockup">
      <span class="brand-dot"></span>
      <span class="brand-name">BRIGHT RIVER POWER</span>
    </div>

    <div class="column-divider"></div>

    <section class="contact-column">
      <h1 class="contact-name">Dennis Halvorsen</h1>
      <ul class="contact-list">
        <li class="contact-item">
          <svg class="contact-icon" viewBox="0 0 16 16"><path d="M4 1l3 3-1.5 2a9 9 0 0 0 4.5 4.5L12 9l3 3-2 2.5C7 14 2 9 1.5 3z" fill="none" stroke="#f7941d" stroke-width="1.4"/></svg>
          0438759164
        </li>
        <li class="contact-item">
          <svg class="contact-icon" viewBox="0 0 16 16"><rect x="1.5" y="3.5" width="13" height="9" fill="none" stroke="#f7941d" stroke-width="1.4"/><path d="M1.5 3.5l6.5 5 6.5-5" fill="none" stroke="#f7941d" stroke-width="1.4"/></svg>
          info@brightriverpower.net.au
        </li>
        <li class="contact-item">
          <svg class="contact-icon" viewBox="0 0 16 16"><circle cx="8" cy="8" r="6.5" fill="none" stroke="#f7941d" stroke-width="1.4"/><ellipse cx="8" cy="8" rx="3" ry="6.5" fill="none" stroke="#f7941d" stroke-width="1.2"/><path d="M1.5 8h13" stroke="#f7941d" stroke-width="1.2"/></svg>
          <span>www.<span class="web-domain">brightriverpower.net.au</span></span>
        </li>
      </ul>
      <ul class="service-list">
        <li class="service-item">solar</li>
        <li class="service-item">Battery storage</li>
        <li class="service-item">LED lighting</li>
        <li class="service-item">Energy saving solutions</li>
        <li class="service-item">General electrical</li>
      </ul>
    </section>
  </article>
</body>
</html>
```